Brivo Australia Dental

I need to update my website and design. I have some ideas in mind and would like to replicate the format from another website into my own. I need the website to be easy to edit (I have no prior wordpress exp) after the design is complete. Please visit https://thelittlenestcare.org.au/ for example of layout.
Target Market(s)
Parents and elder folks
Industry/Entity Type
Dental
Coding
Coded - Design and coding required
Number of Pages Required
4 page
Font styles to use
Sans Serif
Colors
0392cd
Requirements
Must have
- - Home, Services, About Us, News
- - Colours
- - Clear action from viewers
- - Location of business (able to change all the time)
- - Illustrations/ photos

```html
<!DOCTYPE html>
<html lang="en">
<head>
<meta charset="utf-8">
<title>Brivo – For a Better Smile</title>
<link rel="stylesheet" href="https://fonts.googleapis.com/css2?family=Nunito:wght@400;600;700;800&display=swap">
<style>
:root{
  --blue:#0392cd;
  --blue-dark:#0b6fb3;
  --blue-deep:#0a5aa0;
  --blue-light:#4db8e8;
  --ink:#3a3f47;
  --muted:#7b8591;
  --pale:#eef5fa;
  --white:#ffffff;
}
*{margin:0;padding:0;box-sizing:border-box}
html,body{width:1200px;height:3828px;overflow:hidden}
body{font-family:"Nunito",sans-serif;color:var(--ink);background:var(--white);position:relative}
.abs{position:absolute}
a{color:inherit;text-decoration:none}

/* header */
.brand{left:160px;top:16px;color:var(--blue);font-size:58px;font-weight:800;letter-spacing:1px;line-height:1}
.brand-tag{left:166px;top:78px;color:var(--blue);font-size:16px;font-weight:600;letter-spacing:2px}
.nav{left:484px;top:62px;display:flex;gap:46px;font-size:18px;font-weight:700;color:var(--blue)}
.nav a.active{border-bottom:3px solid var(--blue);padding-bottom:4px}
.phone-pill{left:830px;top:0;width:230px;height:48px;background:var(--blue);color:var(--white);border-radius:0 0 24px 24px;display:flex;align-items:center;justify-content:center;gap:10px;font-size:22px;font-weight:700}

/* hero */
.hero-photo{left:0;top:0;width:1200px;height:760px}
.hero-title{left:128px;top:262px;font-size:48px;font-weight:800;color:var(--blue)}
.hero-sub{left:134px;top:326px;font-size:24px;color:var(--blue);font-weight:600}
.btn{display:inline-flex;align-items:center;justify-content:center;border-radius:30px;font-weight:700}
.btn-outline{left:220px;top:378px;width:176px;height:54px;border:2px solid var(--blue);color:var(--blue);font-size:20px;background:rgba(255,255,255,.6)}
.dots{left:286px;top:456px;display:flex;gap:8px}
.dots span{width:14px;height:14px;border-radius:50%;border:2px solid var(--blue)}
.dots span.on{background:var(--blue)}

/* headings */
.sec-title{left:0;width:1200px;text-align:center;font-weight:800;color:var(--blue)}

/* about */
.about-title{top:880px;font-size:50px}
.about-text{left:270px;width:660px;text-align:center;font-size:17px;line-height:26px;color:var(--muted)}
.features{left:180px;top:1116px;width:840px;display:flex;justify-content:space-between}
.feature{width:260px;display:flex;gap:14px}
.feature h4{color:var(--blue);font-size:17px;font-weight:800}
.feature p{font-size:13px;line-height:18px;color:var(--muted)}

/* services */
.services-bg{left:0;top:1290px;width:1200px;height:660px}
.services-title{top:1380px;font-size:42px;color:var(--white)}
.service{width:320px;height:320px;border-radius:50%;text-align:center;color:var(--white);padding-top:80px}
.service h3{font-size:26px;font-weight:800;line-height:32px}
.service p{font-size:13px;line-height:18px;width:210px;margin:14px auto 0;opacity:.9}
.service .go{width:46px;height:46px;border-radius:50%;border:2px solid var(--white);margin:22px auto 0;display:flex;align-items:center;justify-content:center}

/* reviews */
.reviews-title{top:2060px;font-size:40px}
.review-card{left:250px;top:2150px;width:700px;height:210px;background:var(--white);border-radius:105px;box-shadow:0 6px 24px rgba(3,146,205,.25)}
.review-photo{left:280px;top:2170px;width:170px;height:170px;border-radius:50%}
.review-text{left:520px;top:2190px;width:380px;font-size:26px;line-height:34px;color:var(--ink)}
.review-name{left:520px;top:2314px;font-size:18px;color:var(--blue);font-weight:700}
.quote{left:486px;top:2170px;font-size:90px;color:var(--blue-light);font-weight:800;line-height:1}

/* news */
.news-bg{left:0;top:2360px;width:1200px;height:620px}
.news-title{top:2484px;font-size:40px;color:var(--ink)}
.news-card{width:244px;height:340px;background:var(--white);box-shadow:0 4px 18px rgba(0,0,0,.1)}
.news-img{width:244px;height:160px}
.news-date{position:absolute;left:12px;top:168px;width:42px;height:52px;background:var(--blue);color:var(--white);text-align:center;font-size:18px;font-weight:800;line-height:24px;padding-top:2px}
.news-date small{display:block;font-size:10px;line-height:14px;font-weight:600}
.news-head{position:absolute;left:64px;top:170px;width:170px;font-size:14px;line-height:18px;color:var(--blue);font-weight:700}
.news-body{position:absolute;left:12px;top:232px;width:220px;font-size:11px;line-height:15px;color:var(--muted)}
.news-more{position:absolute;left:12px;top:300px;font-size:11px;font-weight:800;color:var(--ink)}

/* why */
.why-photo{left:180px;top:2980px;width:390px;height:300px}
.why-title{left:620px;top:2990px;font-size:40px;font-weight:800;color:var(--blue)}
.why-text{left:620px;top:3056px;width:380px;font-size:17px;line-height:26px;color:var(--muted)}
.btn-solid{left:620px;top:3240px;width:180px;height:52px;background:var(--blue-dark);color:var(--white);font-size:20px}

/* footer */
.footer-bg{left:0;top:3350px;width:1200px;height:478px}
.foot-brand{left:160px;top:3540px;color:var(--white);font-size:60px;font-weight:800;line-height:1}
.foot-tag{left:168px;top:3606px;color:var(--white);font-size:16px;font-weight:600;letter-spacing:2px}
.foot-col{color:var(--white);top:3540px;font-size:14px;line-height:22px}
.foot-col h5{font-size:20px;font-weight:800;margin-bottom:10px}
.socials{display:flex;gap:8px;margin-top:14px}
.socials span{width:30px;height:30px;border-radius:50%;border:2px solid var(--white)}
.foot-bar{left:0;top:3780px;width:1200px;height:48px;background:var(--blue-deep);color:var(--white);font-size:13px;text-align:center;line-height:48px;opacity:.95}
</style>
</head>
<body>

<!-- hero -->
<svg class="abs hero-photo" viewBox="0 0 1200 760" role="img" aria-label="Photo of a smiling family of mother, father and daughter">
  <defs>
    <linearGradient id="heroGrad" x1="0" y1="0" x2="1" y2="0">
      <stop offset="0" stop-color="#f3f7fa"/>
      <stop offset="0.45" stop-color="#e9dcc8"/>
      <stop offset="1" stop-color="#c9c6c0"/>
    </linearGradient>
  </defs>
  <path d="M0 0H1200V560Q600 920 0 560Z" fill="url(#heroGrad)"/>
  <path d="M0 560Q600 920 1200 560V600Q600 960 0 600Z" fill="#0392cd"/>
</svg>

<div class="abs brand">Brivo</div>
<div class="abs brand-tag">for a better smile</div>
<nav class="abs nav">
  <a class="active">Home</a><a>Services</a><a>About Us</a><a>News</a><a>Contact us</a>
</nav>
<div class="abs phone-pill">
  <svg width="20" height="20" viewBox="0 0 24 24"><path fill="#fff" d="M6.6 10.8a15 15 0 006.6 6.6l2.2-2.2a1 1 0 011-.25 11.4 11.4 0 003.6.57 1 1 0 011 1V20a1 1 0 01-1 1A17 17 0 013 4a1 1 0 011-1h3.5a1 1 0 011 1c0 1.25.2 2.45.57 3.57a1 1 0 01-.25 1z"/></svg>
  1300 555 014
</div>

<h1 class="abs hero-title">Welcome to Brivo</h1>
<p class="abs hero-sub">For a Better &amp; Beautiful Smile</p>
<a class="abs btn btn-outline">Book Now</a>
<div class="abs dots"><span class="on"></span><span></span><span></span></div>

<!-- about -->
<h2 class="abs sec-title about-title">About Brivo</h2>
<p class="abs about-text" style="top:964px">Brivo Mobile Dental is a group of Dental Professionals who strongly believes anyone and anywhere can look healthy and fabulous with a bright Smile.</p>
<p class="abs about-text" style="top:1030px">Pellentesque faucibus Ut accumsan ultricies elit Maecenas at justo id velit placerat molestie. Donec dictum lectus non odio Cras a ante vitae enim iaculis aliquam.</p>

<div class="abs features">
  <div class="feature">
    <svg width="44" height="44" viewBox="0 0 44 44" fill="none" stroke="#0392cd" stroke-width="2" style="flex:none"><circle cx="22" cy="12" r="7"/><path d="M8 40c0-9 6-14 14-14s14 5 14 14"/></svg>
    <div><h4>PROFESSIONALISM</h4><p>Our actions do the talking. Our caring and passionate staff will treat all your dental</p></div>
  </div>
  <div class="feature">
    <svg width="44" height="44" viewBox="0 0 44 44" fill="none" stroke="#0392cd" stroke-width="2" style="flex:none"><path d="M6 24l10-8 8 6 14-10"/><path d="M6 30l12 8 20-14"/></svg>
    <div><h4>HONESTY</h4><p>Our word is our promise, our smiling faces. Our patients are our number one priority</p></div>
  </div>
  <div class="feature">
    <svg width="44" height="44" viewBox="0 0 44 44" fill="none" stroke="#0392cd" stroke-width="2" style="flex:none"><path d="M10 8c6-3 9 1 12 1s6-4 12-1c4 3 2 12 0 18-2 6-3 12-6 12s-3-10-6-10-3 10-6 10-4-6-6-12c-2-6-4-15 0-18z"/></svg>
    <div><h4>EDUCATION</h4><p>Our purpose is to Educate anyone and everyone how to create and maintain</p></div>
  </div>
</div>

<!-- services -->
<svg class="abs services-bg" viewBox="0 0 1200 660" aria-hidden="true">
  <defs>
    <radialGradient id="svcGrad" cx="0.5" cy="0.45" r="0.7">
      <stop offset="0" stop-color="#1aa3dc"/><stop offset="1" stop-color="#0a6fb4"/>
    </radialGradient>
  </defs>
  <path d="M0 90Q600 -90 1200 90V560Q600 760 0 560Z" fill="url(#svcGrad)"/>
  <path d="M560 56Q600 80 640 56" fill="none" stroke="#fff" stroke-width="5" stroke-linecap="round"/>
  <circle cx="575" cy="40" r="4" fill="#fff"/><circle cx="625" cy="40" r="4" fill="#fff"/>
</svg>
<h2 class="abs sec-title services-title">Our Services</h2>

<svg class="abs" style="left:170px;top:1470px" width="860" height="420" viewBox="0 0 860 420" aria-hidden="true">
  <path d="M30 200A170 170 0 0 0 370 200" fill="none" stroke="#e5f1f8" stroke-width="34" stroke-linecap="round"/>
  <path d="M490 200A170 170 0 0 0 830 200" fill="none" stroke="#e5f1f8" stroke-width="34" stroke-linecap="round"/>
</svg>
<div class="abs service" style="left:210px;top:1460px;background:#0b78bf">
  <svg width="56" height="56" viewBox="0 0 44 44" fill="none" stroke="#fff" stroke-width="2" style="position:absolute;left:132px;top:18px"><path d="M10 8c6-3 9 1 12 1s6-4 12-1c4 3 2 12 0 18-2 6-3 12-6 12s-3-10-6-10-3 10-6 10-4-6-6-12c-2-6-4-15 0-18z"/></svg>
  <h3>Little Smiles<br>Program</h3>
  <p>Little Smiles Program. Our mobile services are performed within the spacious components</p>
  <div class="go"><svg width="16" height="16" viewBox="0 0 16 16"><path d="M3 6l5 5 5-5" fill="none" stroke="#fff" stroke-width="2"/></svg></div>
</div>
<div class="abs service" style="left:670px;top:1460px;background:#0b78bf">
  <svg width="56" height="56" viewBox="0 0 44 44" fill="none" stroke="#fff" stroke-width="2" style="position:absolute;left:132px;top:18px"><path d="M8 30h28M12 30V18h20v12M14 36l-2 4M30 36l2 4M16 18V10h12v8"/></svg>
  <h3>Golden Years<br>Program</h3>
  <p>Our mobile services are performed within the spacious components of our state of the art mobile clinic</p>
  <div class="go"><svg width="16" height="16" viewBox="0 0 16 16"><path d="M3 6l5 5 5-5" fill="none" stroke="#fff" stroke-width="2"/></svg></div>
</div>

<!-- reviews -->
<h2 class="abs sec-title reviews-title">Our Reviews</h2>
<svg class="abs" style="left:166px;top:2232px" width="30" height="50" viewBox="0 0 30 50"><path d="M24 4L6 25l18 21" fill="none" stroke="#9aa3ad" stroke-width="4"/></svg>
<svg class="abs" style="left:1004px;top:2232px" width="30" height="50" viewBox="0 0 30 50"><path d="M6 4l18 21L6 46" fill="none" stroke="#9aa3ad" stroke-width="4"/></svg>
<div class="abs review-card"></div>
<div class="abs review-photo" role="img" aria-label="Photo of a patient with a dental team member" style="background:linear-gradient(135deg,#6d8fae,#b9a58c)"></div>
<div class="abs quote">“</div>
<p class="abs review-text">Dr Lewin is very nice and fun to talk to. She makes my teeth feel strong and clean</p>
<p class="abs review-name">Marco</p>

<!-- news -->
<svg class="abs news-bg" viewBox="0 0 1200 620" aria-hidden="true">
  <path d="M0 210Q600 -110 1200 210V620H0Z" fill="#eef5fa"/>
  <path d="M0 210Q600 -110 1200 210" fill="none" stroke="#0392cd" stroke-width="14"/>
</svg>
<h2 class="abs sec-title news-title">News &amp; Blogs</h2>

<div class="abs news-card" style="left:164px;top:2556px">
  <div class="news-img" role="img" aria-label="Photo of the mobile dental clinic truck" style="background:linear-gradient(135deg,#9fc4de,#d7e4ea)"></div>
  <div class="news-date">02<small>JAN</small></div>
  <div class="news-head">Pellentesque faucibus Ut accumsan ultric</div>
  <p class="news-body">Sed ut perspiciatis unde omnis iste natus error sit voluptatem accusantium doloremque laudantium totam rem aperiam.</p>
  <a class="news-more">READ MORE</a>
</div>
<div class="abs news-card" style="left:478px;top:2556px">
  <div class="news-img" role="img" aria-label="Photo of the inside of a dental clinic" style="background:linear-gradient(135deg,#c96a3c,#e2b28f)"></div>
  <div class="news-date">30<small>DEC</small></div>
  <div class="news-head">Pellentesque faucibus Ut accumsan ultric</div>
  <p class="news-body">Nemo enim ipsam voluptatem quia voluptas sit aspernatur aut odit aut fugit sed quia consequuntur magni dolores.</p>
  <a class="news-more">READ MORE</a>
</div>
<div class="abs news-card" style="left:792px;top:2556px">
  <div class="news-img" role="img" aria-label="Photo of dental staff standing together" style="background:linear-gradient(135deg,#3d5b7c,#a48a74)"></div>
  <div class="news-date">23<small>DEC</small></div>
  <div class="news-head">Pellentesque faucibus Ut accumsan ultric</div>
  <p class="news-body">Neque porro quisquam est qui dolorem ipsum quia dolor sit amet consectetur adipisci velit sed quia non numquam.</p>
  <a class="news-more">READ MORE</a>
</div>

<!-- why choose us -->
<div class="abs why-photo" role="img" aria-label="Photo of a modern dental treatment room with chair" style="background:linear-gradient(135deg,#dfe6ea,#8fa3b2)"></div>
<h2 class="why-title abs">Why Choose Us</h2>
<p class="abs why-text">Pellentesque faucibus Ut accumsan ultricie elit Maecenas at justo id velit placerat molestie Donec dictum lectus non odio Cras a ante vitae. Mauris nunc sed nunc venenatis et tristique eu imperdiet ac nisl Cum sociis natoque penatibus et.</p>
<a class="abs btn btn-solid">Learn More</a>

<!-- footer -->
<svg class="abs footer-bg" viewBox="0 0 1200 478" aria-hidden="true">
  <defs>
    <linearGradient id="footGrad" x1="0" y1="0" x2="0" y2="1">
      <stop offset="0" stop-color="#1a9ad6"/><stop offset="1" stop-color="#0a6fb4"/>
    </linearGradient>
  </defs>
  <path d="M0 80Q600 -40 1200 80V478H0Z" fill="url(#footGrad)"/>
</svg>
<div class="abs foot-brand">Brivo</div>
<div class="abs foot-tag">for a better smile</div>

<div class="abs foot-col" style="left:430px">
  <h5>Quick Links</h5>
  <div>Home</div><div>Services</div><div>About Us</div><div>News</div><div>Contact us</div>
</div>
<div class="abs foot-col" style="left:600px;width:200px">
  <h5>Contact Us</h5>
  <div style="display:flex;gap:8px"><svg width="14" height="20" viewBox="0 0 14 20" style="flex:none;margin-top:2px"><path d="M7 0a7 7 0 017 7c0 5-7 13-7 13S0 12 0 7a7 7 0 017-7z" fill="#fff"/><circle cx="7" cy="7" r="2.5" fill="#0a6fb4"/></svg><span>Harlow Public School,<br>12 Elm Street, Harlow<br>NSW 2000</span></div>
  <div style="display:flex;gap:8px;margin-top:8px"><svg width="14" height="14" viewBox="0 0 24 24" style="margin-top:4px"><path fill="#fff" d="M6.6 10.8a15 15 0 006.6 6.6l2.2-2.2a1 1 0 011-.25 11.4 11.4 0 003.6.57 1 1 0 011 1V20a1 1 0 01-1 1A17 17 0 013 4a1 1 0 011-1h3.5a1 1 0 011 1c0 1.25.2 2.45.57 3.57a1 1 0 01-.25 1z"/></svg>1300 555 014</div>
</div>
<div class="abs foot-col" style="left:830px">
  <h5>Opening hours</h5>
  <div>Mon: 8AM to 4PM</div><div>Thurs: 8AM to 4PM</div><div>Fri: 8AM to 4PM</div>
  <div class="socials"><span></span><span></span><span></span><span></span></div>
</div>
<div class="abs foot-bar">© 2018 Company Name. All right reserved.</div>

</body>
</html>
```